female esthetician looking for an impact business card

I an an expert in skin care industry with high experience in NYC.I want my business card to look professional , an impact at first look. I do want a combination between white and gold . I believe the font will be great if is gold.. The Fonts are also important. MIRABELA COSTINA (SKIN CARE BOUTIQUE)

THIS SHOULD BE THE BUSINESS NAME, and should be placed on th eback of the card.
IN front m, the name MIRABELA COSTINA - ESTHETCIAN

BY APPOINTMENTS ONLY: 518.240.7136

Target Market(s)

HIGH END CLIENTELE

Contact Information for Business Card

iT WILL BE on a luxury paper. I neeed the wow feeling

Requirements
Should not have
• pictures

```html
<!DOCTYPE html>
<html lang="en">
<head>
<meta charset="utf-8">
<title>Mirabela Costina – Business Card</title>
<link href="https://fonts.googleapis.com/css2?family=Questrial&family=Open+Sans:wght@400;700&display=swap" rel="stylesheet">
<style>
  :root {
    --bg: #2a2a2c;
    --gold-dark: #9a6e2c;
    --gold-mid: #c9a13f;
    --gold-light: #d8b453;
    --gold-text: #b0863a;
    --ink: #1c1c1c;
    --paper: #ffffff;
  }
  * { margin: 0; padding: 0; box-sizing: border-box; }
  html, body { width: 1200px; height: 800px; overflow: hidden; }
  body {
    background: var(--bg);
    display: flex;
    align-items: center;
    justify-content: center;
    gap: 80px;
  }
  .card {
    position: relative;
    width: 440px;
    height: 440px;
    border-radius: 34px;
    overflow: hidden;
  }
  .card--front {
    background: linear-gradient(160deg, var(--gold-dark) 0%, var(--gold-mid) 45%, var(--gold-light) 55%, var(--gold-dark) 100%);
    display: flex;
    flex-direction: column;
    align-items: center;
    justify-content: center;
    color: var(--paper);
  }
  .card--back { background: var(--paper); }

  .brand-name {
    font-family: "Questrial", sans-serif;
    font-size: 38px;
    line-height: 1.1;
    font-weight: 400;
  }
  .tagline {
    font-family: "Questrial", sans-serif;
    font-size: 14px;
    letter-spacing: 1px;
    margin-top: 8px;
  }

  .card--back .identity {
    position: absolute;
    right: 40px;
    top: 56px;
    text-align: right;
  }
  .card--back .brand-name { color: var(--gold-text); }
  .card--back .tagline { color: var(--ink); }

  .contact {
    position: absolute;
    left: 40px;
    top: 180px;
    font-family: "Open Sans", sans-serif;
    font-size: 15px;
    line-height: 1.6;
    color: var(--ink);
  }
  .contact__label { font-weight: 700; }
  .contact__web { margin-top: 10px; font-weight: 700; }

  .base-band {
    position: absolute;
    left: 0;
    bottom: 0;
    width: 100%;
    height: 56px;
    background: linear-gradient(90deg, var(--gold-dark), var(--gold-light));
    border-top: 3px solid var(--ink);
  }
</style>
</head>
<body>
  <section class="card card--front" aria-label="Card front">
    <p class="brand-name">Mirabela Costina</p>
    <p class="tagline">Skin Care Expert</p>
  </section>

  <section class="card card--back" aria-label="Card back">
    <div class="identity">
      <p class="brand-name">Mirabela Costina</p>
      <p class="tagline">Skin Care Expert</p>
    </div>
    <div class="contact">
      <p><span class="contact__label">P:</span> 518.240.7136</p>
      <p><span class="contact__label">E:</span> hello@mirabelaskin.com</p>
      <p>210 Laurel Avenue, Suite 4, Brookhaven</p>
      <p>NY 11719 USA</p>
      <p class="contact__web">www.mirabelaskin.com</p>
    </div>
    <div class="base-band"></div>
  </section>
</body>
</html>
```